Business Cards for company that supports physicians that do medical research

Need to create a business card for Qorvel Studies (www.qorvelstudies.example), a company devoted to supporting physicians who conduct medical research. The form of the card should match the message of research and information quest. I have provided the logo of the company as an uploaded file. Designs should be simple and slick aimed at very high end clients.

Target Market(s)

Medical doctors that are also researchers

Industry/Entity Type

Medical

Contact Information for Business Card

Should feature logo and fields for personal info:
Name/title
Phone /email

Font styles to use
Serif
Sans Serif

Requirements
Must have
• Qorvel logo and fields for personal info:
• Name: Bertrand Okonfu
• Title: VP Research and Senior Analyst
• Phone: 555-203-4719
• email: info@qorvelstudies.example
Nice to have
• Interesting cards that I've seen:
• 1- all black/charcoal or very dark background
• 2- Plastic - semi-transparent
• 3- non-standard height-width ratios
• 4- Functional cards -- USB drive incorporated
Should not have
• Too busy; needs to stay very simple

```html
<!DOCTYPE html>
<html lang="en">
<head>
<meta charset="utf-8">
<title>Qorvel Studies — Business Card</title>
<link href="https://fonts.googleapis.com/css2?family=Open+Sans:wght@400;600&display=swap" rel="stylesheet">
<style>
  :root {
    --backdrop: #c2c2c2;
    --card-front: #000000;
    --card-back: #1a84c5;
    --accent-blue: #2a90d8;
    --text-light: #ffffff;
    --wordmark-grey: #8a8a8a;
  }
  * { margin: 0; padding: 0; box-sizing: border-box; }
  html, body {
    width: 1200px;
    height: 900px;
    overflow: hidden;
  }
  body {
    background: var(--backdrop);
    font-family: "Open Sans", Arial, sans-serif;
    position: relative;
  }
  .card {
    position: absolute;
    top: 184px;
    width: 302px;
    height: 490px;
    border-radius: 12px;
  }
  .card-front {
    left: 299px;
    background: var(--card-front);
  }
  .card-back {
    left: 646px;
    width: 304px;
    background: var(--card-back);
  }
  .wordmark {
    position: absolute;
    font-weight: 600;
    white-space: nowrap;
    letter-spacing: 0.5px;
  }
  .card-front .wordmark {
    left: 40px;
    top: 118px;
    font-size: 30px;
    color: var(--accent-blue);
  }
  .card-back .wordmark {
    left: 40px;
    top: 350px;
    font-size: 30px;
    color: var(--text-light);
  }
  .identity {
    position: absolute;
    left: 0;
    right: 0;
    top: 280px;
    text-align: center;
  }
  .person-name {
    font-size: 17px;
    font-weight: 600;
    color: var(--accent-blue);
    line-height: 24px;
  }
  .person-title {
    font-size: 12.5px;
    color: var(--text-light);
    line-height: 20px;
  }
  .contact {
    position: absolute;
    left: 0;
    right: 0;
    top: 378px;
    text-align: center;
    font-size: 13px;
    color: var(--text-light);
    line-height: 21px;
  }
  .contact-line {
    display: flex;
    justify-content: center;
    align-items: center;
    gap: 4px;
  }
  .contact-icon {
    width: 10px;
    height: 10px;
    fill: var(--accent-blue);
  }
</style>
</head>
<body>
  <section class="card card-front" aria-label="Business card front">
    <div class="wordmark">Qorvel Studies</div>
    <div class="identity">
      <p class="person-name">Bertrand Okonfu</p>
      <p class="person-title">VP Research and Senior Analyst</p>
    </div>
    <div class="contact">
      <p class="contact-line">
        <svg class="contact-icon" viewBox="0 0 10 10" aria-hidden="true">
          <path d="M1 3.2 C1 2 2.5 1.5 5 1.5 S9 2 9 3.2 L7.4 3.8 L6.8 3 H3.2 L2.6 3.8 Z M2.8 4.5 H7.2 L8.3 8.5 H1.7 Z"/>
        </svg>
        <span>555-203-4719</span>
      </p>
      <p class="contact-line">
        <svg class="contact-icon" viewBox="0 0 10 10" aria-hidden="true">
          <path d="M0.5 2 H9.5 V8 H0.5 Z M1 2.4 L5 5.6 L9 2.4" stroke="#000" stroke-width="0.7"/>
        </svg>
        <span>info@qorvelstudies.example</span>
      </p>
    </div>
  </section>

  <section class="card card-back" aria-label="Business card back">
    <div class="wordmark">Qorvel Studies</div>
  </section>
</body>
</html>
```